Real Estate Business Card

On the front side I want to have my info, my brokerage info.
On the back side I want have my complany’s logo, website and Facebook link. I will provide all this once I select a design.

I would like to see Black background and gold text, Dark Blue and gold text and White and blue text designs

Font styles to use
Sans Serif
Script

```html
<!DOCTYPE html>
<html lang="en">
<head>
<meta charset="utf-8">
<title>Harbor Lane Realty – Business Card</title>
<link href="https://fonts.googleapis.com/css2?family=Cinzel:wght@600&family=Open+Sans:wght@400;600&display=swap" rel="stylesheet">
<style>
  :root {
    --backdrop: #2b2b2b;
    --card-front: #ededed;
    --card-back: #f7f7f8;
    --brand-blue: #2350a6;
    --ink: #333333;
    --rule: #a9a9a9;
    --white: #ffffff;
  }
  * { margin: 0; padding: 0; box-sizing: border-box; }
  html, body { width: 1200px; height: 1200px; overflow: hidden; }
  body {
    background: var(--backdrop);
    position: relative;
    font-family: "Open Sans", Arial, sans-serif;
    color: var(--ink);
  }
  .card {
    position: absolute;
    top: 310px;
    width: 366px;
    height: 594px;
    box-shadow: 0 4px 10px rgba(0,0,0,0.5);
    text-align: center;
  }
  .card--front { left: 233px; background: var(--card-front); }
  .card--back  { left: 628px; background: var(--card-back); width: 368px; }

  .wordmark {
    position: absolute;
    left: 0; right: 0;
    color: var(--brand-blue);
    font-family: "Cinzel", Georgia, serif;
    font-weight: 600;
  }
  .wordmark__name { display: block; font-size: 40px; line-height: 44px; letter-spacing: 1px; }
  .wordmark__sub  { display: block; font-size: 20px; line-height: 26px; letter-spacing: 6px; }
  .card--front .wordmark { top: 170px; }
  .card--back .wordmark  { top: 220px; }

  .person {
    position: absolute;
    left: 0; right: 0;
    top: 338px;
  }
  .person__name {
    font-family: "Cinzel", Georgia, serif;
    font-weight: 600;
    color: var(--brand-blue);
    font-size: 23px;
    line-height: 30px;
  }
  .person__role { font-size: 17px; line-height: 22px; }
  .divider {
    width: 208px;
    height: 1px;
    background: var(--rule);
    margin: 9px auto 9px;
  }
  .contact { list-style: none; font-size: 17px; line-height: 21.5px; }
  .contact__label { color: var(--brand-blue); font-weight: 600; }
  .address { font-size: 17px; line-height: 21.5px; }

  .web-strip {
    position: absolute;
    left: 0; right: 0;
    top: 356px;
    height: 53px;
    border-top: 3px solid var(--brand-blue);
    border-bottom: 3px solid var(--brand-blue);
    font-size: 17px;
    font-weight: 600;
    line-height: 47px;
    letter-spacing: 0.5px;
  }
  .social-band {
    position: absolute;
    left: 0; right: 0;
    top: 480px;
    height: 61px;
    background: var(--brand-blue);
    color: var(--white);
    font-size: 17px;
    line-height: 61px;
  }
</style>
</head>
<body>
  <section class="card card--front">
    <div class="wordmark">
      <span class="wordmark__name">Harbor Lane</span>
      <span class="wordmark__sub">Realty</span>
    </div>
    <div class="person">
      <h1 class="person__name">Daniel Marsh</h1>
      <p class="person__role">Managing Director</p>
      <div class="divider"></div>
      <ul class="contact">
        <li><span class="contact__label">P:</span> 044-555 010 234</li>
        <li><span class="contact__label">M:</span> 044-555 010 234</li>
        <li><span class="contact__label">F:</span> 044-555 010 234</li>
        <li><span class="contact__label">E:</span> info@harborlane.com</li>
      </ul>
      <div class="divider"></div>
      <p class="address">48 Quayside Road, Suite 2<br>Portmere, 204816.</p>
    </div>
  </section>

  <section class="card card--back">
    <div class="wordmark">
      <span class="wordmark__name">Harbor Lane</span>
      <span class="wordmark__sub">Realty</span>
    </div>
    <div class="web-strip">WWW.HARBORLANE.COM</div>
    <div class="social-band">social: /harborlanerealty</div>
  </section>
</body>
</html>
```